Counseling Practice Business Card

I need a professional looking business card incorporating my new logo that was just completed. Card needs to incorporate my name and title, description of my specialty, my address, my phone number, my fax number, my email and my website URL. I need to be able to choose design on/with different paper colors and textures.
I do not have a lot of business card ideas so I am open to anything but I want bold,sharp, clear card without additional designs other than my logo (see attached file info). I am open to different color backgrounds or paper colors including black. I do not like traditional brackets around area codes in phone number or dashes between numbers in phone number. Am open to other ways of presenting including periods between numbers as appropriate. I do not know enough to know what I like yet but I want card to coordinate and work together with my logo. My practice emphasizes natural mental health interventions so any use of color (with background paper color or the blue and green in my logo) that elicits nature is nice. In addition to black, any natural brown or wood looking background might be desirable also. Most of the offerings so far look very similar and boring.

Target Market(s)

Potential therapy clients and other professionals

Contact Information for Business Card

Card information:
Gerald M. Whitcombe, Ph.D.
Licensed Clinical Psychologist
Integrative Health Coach
4812 Marlowe Ridge Blvd SE
Suite 310
Alder Grove, GA 30188
(770) 415-2983 phone
(770) 581-4096 fax
drgeraldwhitcombe@quillmarsh.net
brightfernwellness.net

Font styles to use
Serif
Sans Serif
Other font styles liked:
• anything that you think looks crisp, clear and easily readable

Requirements
Must have
• Any color used should coordinate with my logo design (see attached files).
• Card should be printed horizontally so top and bottom are longest sides of rectangle.
• Background color or paper color should complement and highlight logo. Do not like a white background. black, grey, brown or any color my logo would blend well with.
Nice to have
• I would like designer to utilize color to highlight letters/name or phone-fax-web symbols.
• Bottom edge of card could be highlighted if appropriate to an idea.
Should not have
• I would NOT want the card to have a pure white background at all.
• No clear cards.
• Cards should be oriented with long sides on bottom and top, NOT sides. DO NOT LIKE THIS THIN TALL ORIENTATION.

```html
<!DOCTYPE html>
<html lang="en">
<head>
<meta charset="utf-8">
<title>Brightfern Wellness – Business Card</title>
<link href="https://fonts.googleapis.com/css2?family=Open+Sans:wght@400;600&family=Roboto+Condensed:wght@700&display=swap" rel="stylesheet">
<style>
  :root{
    --stage:#2a2a2c;
    --card:#1c1c1e;
    --blue:#2a78c0;
    --green:#0b6b34;
    --text-light:#d6d6d6;
    --white:#ffffff;
    --ghost:rgba(42,120,192,0.09);
  }
  html,body{margin:0;padding:0;overflow:hidden;}
  body{width:1200px;height:960px;background:var(--stage);position:relative;font-family:"Open Sans",Arial,sans-serif;}
  .card{position:absolute;left:302px;width:598px;height:343px;background:var(--card);overflow:hidden;box-shadow:0 2px 8px rgba(0,0,0,.5);}
  .card--front{top:122px;}
  .card--back{top:497px;}
  .card__shapes{position:absolute;inset:0;}
  .ghost-name{position:absolute;left:10px;top:175px;font-size:46px;font-weight:600;color:var(--ghost);white-space:nowrap;transform:rotate(-28deg);transform-origin:left bottom;}
  .contact{position:absolute;left:40px;top:36px;margin:0;padding:0;list-style:none;color:var(--text-light);font-size:14.5px;line-height:19px;}
  .contact li{display:flex;align-items:flex-start;}
  .contact .gap{margin-top:10px;}
  .contact svg{width:12px;height:12px;margin:3px 14px 0 0;flex:none;fill:var(--blue);}
  .contact .noicon{margin-left:26px;}
  .identity{position:absolute;right:29px;bottom:20px;text-align:right;color:var(--white);}
  .identity__name{font-family:"Roboto Condensed",Arial,sans-serif;font-weight:700;font-size:18px;text-transform:uppercase;margin:0 0 4px;letter-spacing:-.2px;}
  .identity__title{font-size:15.5px;line-height:21px;margin:0;}
  .brand{position:absolute;left:0;right:0;top:146px;display:flex;justify-content:center;align-items:center;gap:12px;}
  .brand__dot{width:24px;height:24px;border-radius:50%;background:var(--blue);}
  .brand__name{font-size:38px;font-weight:600;color:var(--blue);letter-spacing:.5px;}
</style>
</head>
<body>
  <section class="card card--front" aria-label="Business card front">
    <div class="ghost-name">Brightfern Wellness</div>
    <svg class="card__shapes" viewBox="0 0 598 343" width="598" height="343" aria-hidden="true">
      <path d="M150,343 C385,245 548,120 544,40 C543,20 538,8 530,0 L598,0 L598,343 Z" fill="var(--green)"/>
      <path d="M213,343 C410,255 552,125 551,45 C550,22 543,8 533,0 L598,0 L598,343 Z" fill="var(--blue)"/>
    </svg>
    <ul class="contact">
      <li><svg viewBox="0 0 12 12"><path d="M6 0a4 4 0 0 0-4 4c0 3 4 8 4 8s4-5 4-8a4 4 0 0 0-4-4zm0 5.5A1.5 1.5 0 1 1 6 2.5a1.5 1.5 0 0 1 0 3z"/></svg>4812 Marlowe Ridge Blvd SE</li>
      <li><span class="noicon">Suite 310, Alder Grove, GA 30188</span></li>
      <li class="gap"><svg viewBox="0 0 12 12"><path d="M1 3c0-1 1-2 5-2s5 1 5 2v1H8V3H4v1H1zM2 6l2-2h4l2 2v5H2zm4 1a1.5 1.5 0 1 0 0 3 1.5 1.5 0 0 0 0-3z"/></svg>(770) 415-2983</li>
      <li><svg viewBox="0 0 12 12"><path d="M3 1h6v3H3zM1 5h10v5H9V8H3v2H1zM3 9h6v2H3z"/></svg>(770) 581-4096</li>
      <li><svg viewBox="0 0 12 12"><path d="M1 3h10v6H1zM1 3l5 3.5L11 3"/></svg>drgeraldwhitcombe@quillmarsh.net</li>
      <li><svg viewBox="0 0 12 12"><circle cx="6" cy="6" r="5"/></svg>www.brightfernwellness.net</li>
    </ul>
    <div class="identity">
      <p class="identity__name">Gerald M. Whitcombe, Ph.D.</p>
      <p class="identity__title">Licensed Clinical Psychologist</p>
      <p class="identity__title">Integrative Health Coach</p>
    </div>
  </section>

  <section class="card card--back" aria-label="Business card back">
    <div class="brand">
      <span class="brand__dot"></span>
      <span class="brand__name">Brightfern Wellness</span>
    </div>
  </section>
</body>
</html>
```